Suds Haven Laundromat Wordpress Design

We need a Wordpress website design for our laundromat, Suds Haven Atlanta, at www.sudshavenatlanta-example.com. We would like to have 6 pages: Home, About Us, Services, Locations, Reviews and Contact us. We will provide content for the text on each page. What we do: We are a full service laundromat that provides dry cleaning drop off, professional laundry services, wash dry fold and self service laundry to the local community. We would like to use the color scheme from our logo to convey a warm, safe, and bright business that caters to its diverse community.
Updates

I like the structure of this laundromat website: http://www.washtroveusa-example.com/ Using my logo and color scheme in the above referenced website is what. Am looking for. The photos attached to the project with the female model should be used as a primary focus and supplemented by actual photos of the equipment.

Target Market(s)

Our target market is a diverse group of people from Midtown Atlanta - LGBTQ community /Locals/Regulars that have been coming to laundromat for 30 years.

Industry/Entity Type

Laundromat

Coding

Coded - Design and coding required

Number of Pages Required

5+ page

Font styles to use
Sans Serif

Colors
0054AA
0677BA
7BADD7
CADEEF
E8F1F8

Requirements
Must have
• Feature this video on the main page: https://videohost-example.com/xq7Rm2bPz4k

```html
<!DOCTYPE html>
<html lang="en">
<head>
<meta charset="utf-8">
<title>Suds Haven Atlanta</title>
<link href="https://fonts.googleapis.com/css2?family=Bebas+Neue&family=Montserrat:wght@400;500;600;700&display=swap" rel="stylesheet">
<style>
:root{
  --blue-deep:#0054AA;
  --blue-mid:#0677BA;
  --blue-accent:#0d9ad6;
  --blue-soft:#7BADD7;
  --blue-pale:#CADEEF;
  --band:#f1f5f9;
  --footer:#2e4a72;
  --ink:#222;
  --text:#3a3a3a;
  --grey-circle:#d9d9d9;
}
*{margin:0;padding:0;box-sizing:border-box}
html,body{width:1200px;height:2970px;overflow:hidden;background:#fff}
body{position:relative;font-family:"Montserrat",sans-serif;color:var(--text)}
.abs{position:absolute}
/* header */
.site-header{position:absolute;left:0;top:0;width:1200px;height:76px;background:#fff}
.brand{position:absolute;left:104px;top:22px;display:flex;align-items:center;gap:10px}
.brand-dot{width:22px;height:22px;border-radius:50%;background:var(--blue-deep)}
.brand-name{font-weight:700;font-size:26px;color:var(--blue-deep);letter-spacing:.5px}
.main-nav a{position:absolute;top:0;height:76px;line-height:84px;font-size:12.5px;color:#222;text-decoration:none;letter-spacing:.2px;white-space:nowrap}
.main-nav a.active{font-weight:500}
.main-nav a.active::after{content:"";position:absolute;left:0;right:-4px;bottom:0;height:4px;background:var(--blue-deep)}
.nav-divider{position:absolute;left:1029px;top:20px;width:2px;height:36px;background:var(--blue-deep)}
.social-top{position:absolute;left:1046px;top:31px;font-size:11px;font-weight:700;color:#111;letter-spacing:.5px;white-space:nowrap}
/* hero */
.hero{position:absolute;left:0;top:76px;width:1200px;height:600px;background:linear-gradient(180deg,#b7d2cc 0%,#9fb7b4 30%,#c9c7c0 60%,#8d8e90 100%)}
.hero-wave{position:absolute;left:0;top:560px;width:1200px;height:120px}
/* headings */
.sec-title{font-family:"Bebas Neue",sans-serif;font-weight:400;font-size:36px;color:var(--ink);letter-spacing:.3px;line-height:1}
.sec-title span{color:var(--blue-deep)}
.title-bar{width:46px;height:2px;background:var(--blue-accent);margin-top:10px}
/* about */
.about-copy{position:absolute;left:573px;top:782px;width:468px}
.about-copy p{font-size:13px;line-height:27px}
.about-copy .lead{margin-top:24px}
.about-copy p + p{margin-top:4px}
.btn{display:inline-block;margin-top:22px;width:150px;height:42px;line-height:42px;text-align:center;background:#0aa3dd;color:#fff;font-size:13px;font-weight:600;text-decoration:none}
/* services */
.services{position:absolute;left:0;top:1264px;width:1200px;height:596px;background:var(--band)}
.service{position:absolute;width:245px}
.service svg{display:block}
.service h3{font-family:"Bebas Neue",sans-serif;font-weight:400;font-size:19px;color:var(--blue-deep);margin-top:12px;letter-spacing:.2px}
.service p{font-size:11px;line-height:19px;color:#333;margin-top:6px}
.service .more{color:var(--blue-accent)}
/* testimonials */
.testimonials-title{position:absolute;left:0;top:1934px;width:1200px;text-align:center}
.testimonials-title .title-bar{margin:10px auto 0;width:60px}
.card{position:absolute;top:2063px;width:277px;height:220px;background:#fff;box-shadow:0 6px 14px rgba(0,0,0,.07);text-align:center}
.quote-badge{position:absolute;left:50%;top:-43px;width:88px;height:88px;margin-left:-44px;border-radius:50%;background:var(--grey-circle);border:4px solid #fff;box-shadow:0 2px 6px rgba(0,0,0,.12);display:flex;align-items:center;justify-content:center;color:#fff;font-weight:700;font-size:40px;line-height:1}
.quote-badge.active{background:var(--blue-deep)}
.card h4{margin-top:65px;font-size:16.5px;font-weight:500;color:var(--blue-deep)}
.card p{font-size:11.2px;line-height:23px;color:#333;padding:0 14px;margin-top:10px}
.card-plus{position:absolute;left:50%;bottom:-12px;margin-left:-21px;width:42px;height:21px;border-radius:21px 21px 0 0;background:var(--blue-deep);color:#fff;font-size:16px;font-weight:700;line-height:22px}
.dots{position:absolute;top:2323px;left:564px;display:flex;gap:9px}
.dots i{width:11px;height:11px;border-radius:50%;border:1.5px solid var(--blue-deep);display:block}
.dots i.on{background:var(--blue-deep)}
/* footer */
.site-footer{position:absolute;left:0;top:2412px;width:1200px;height:558px;background:var(--footer);color:#fff}
.footer-brand{position:absolute;left:0;top:95px;width:1200px;text-align:center;font-weight:700;font-size:40px;letter-spacing:1px}
.footer-line{position:absolute;height:1px;background:rgba(255,255,255,.18)}
.footer-nav a{position:absolute;top:227px;font-size:15px;color:#fff;text-decoration:none;white-space:nowrap}
.soc{position:absolute;top:222px;width:30px;height:30px;border-radius:50%;background:#fff;color:var(--footer);font-size:11px;font-weight:700;text-align:center;line-height:30px}
.contact-line{position:absolute;font-size:13.8px;line-height:24px}
.hours{position:absolute;left:611px;top:306px;font-size:13.8px;line-height:24px}
.hours .note{color:#1fa8e6;font-weight:500}
.copyright{position:absolute;left:0;top:460px;width:1200px;text-align:center;font-size:12.5px}
.copyright b{font-weight:600}
</style>
</head>
<body>

<header class="site-header">
  <div class="brand"><span class="brand-dot"></span><span class="brand-name">Suds Haven</span></div>
  <nav class="main-nav">
    <a class="active" href="#" style="left:416px">HOME</a>
    <a href="#" style="left:497px">ABOUT US</a>
    <a href="#" style="left:605px">SERVICES</a>
    <a href="#" style="left:709px">LOCATION</a>
    <a href="#" style="left:826px">REVIEWS</a>
    <a href="#" style="left:926px">CONTACT US</a>
  </nav>
  <div class="nav-divider"></div>
  <div class="social-top">Fb&nbsp;&nbsp;Tw</div>
</header>

<section class="hero" role="img" aria-label="Photo of a woman in a blue dress walking through a laundromat lined with front-load washers, shop name sign on the wall"></section>
<svg class="hero-wave" viewBox="0 0 1200 120" preserveAspectRatio="none" aria-hidden="true">
  <path d="M0 30 Q600 105 1200 0 L1200 120 L0 120 Z" fill="#fff"/>
  <path d="M0 48 Q560 140 1150 54" fill="none" stroke="var(--blue-deep)" stroke-width="7"/>
</svg>

<!-- about -->
<svg class="abs" style="left:155px;top:740px" width="390" height="440" viewBox="0 0 390 440" aria-hidden="true">
  <path d="M340 165 A172 172 0 1 0 180 410" fill="none" stroke="var(--blue-deep)" stroke-width="6" transform="translate(-10,-15)"/>
  <circle cx="222" cy="16" r="9" fill="none" stroke="var(--blue-deep)" stroke-width="5"/>
  <circle cx="160" cy="45" r="5" fill="none" stroke="var(--blue-deep)" stroke-width="3.5"/>
  <circle cx="274" cy="43" r="5" fill="none" stroke="var(--blue-deep)" stroke-width="3.5"/>
</svg>
<div class="abs" role="img" aria-label="Close-up photo of a stainless steel front-load washer with clothes tumbling inside" style="left:180px;top:826px;width:307px;height:307px;border-radius:50%;background:radial-gradient(circle at 50% 50%,#8f969c 0%,#b7bcc0 45%,#6f757a 100%)"></div>
<div class="abs" role="img" aria-label="Photo of a pay-by-phone sign on a machine" style="left:370px;top:1005px;width:168px;height:168px;border-radius:50%;border:7px solid #fff;box-shadow:0 3px 10px rgba(0,0,0,.25);background:radial-gradient(circle,#f4f6f7 0%,#dfe3e5 100%)"></div>

<div class="about-copy">
  <h2 class="sec-title">About <span>Us</span></h2>
  <div class="title-bar"></div>
  <p class="lead">Suds Haven is family-owned laundromat that has been serving Midtown, GA for over 45 years. We are proud to offer high quality and convenient services to the area residents and business owners and strive to keep our customers clothing in tip top shape.</p>
  <p>Whether you have commercial laundry needs, are washing clothes for your family, or want to relax that weekend and have us pick up and wash/dry/fold for you, the professionals at Suds Haven are ready to meet your goals.</p>
  <a class="btn" href="#">Contact Us Today</a>
</div>

<!-- services -->
<section class="services">
  <div class="abs" style="left:162px;top:78px">
    <h2 class="sec-title">Our <span>Services</span></h2>
    <div class="title-bar"></div>
  </div>

  <div class="service" style="left:162px;top:158px">
    <svg width="62" height="62" viewBox="0 0 62 62" fill="none" stroke="var(--blue-deep)" stroke-width="2">
      <path d="M18 14 L31 10 L44 14 L58 22 L58 60 M18 14 L4 22 L4 60 M14 30 V60 M48 30 V60"/>
      <path d="M24 12 L31 26 L38 12"/><rect x="36" y="36" width="8" height="8"/>
    </svg>
    <h3>Wash Dry Fold</h3>
    <p>Tired, too much to do, own a business and need linens, sheets, towels, etc., cleaned? Don't worry, we can do your laundry...<span class="more">[+]</span></p>
  </div>
  <div class="service" style="left:435px;top:158px">
    <svg width="62" height="62" viewBox="0 0 62 62" fill="none" stroke="var(--blue-deep)" stroke-width="2">
      <path d="M8 14 L20 8 L32 14 Z M30 14 L42 8 L54 14 Z"/>
      <rect x="2" y="22" width="30" height="38"/><line x1="2" y1="30" x2="32" y2="30"/><circle cx="17" cy="45" r="9"/>
      <path d="M36 30 H58 M40 38 L58 60 M58 38 L40 60"/>
    </svg>
    <h3>Professional Laundry Services</h3>
    <p>If you want to enjoy the perks of dry cleaning without all the chemicals, we offer a wash, dry, and press/iron service...[+]</p>
  </div>
  <div class="service" style="left:162px;top:360px">
    <svg width="62" height="62" viewBox="0 0 62 62" fill="none" stroke="var(--blue-deep)" stroke-width="2">
      <path d="M4 60 V28 L20 20 L30 28 V60 Z"/><path d="M32 60 V22 L46 14 L60 22 V60 Z"/>
      <line x1="46" y1="14" x2="46" y2="2"/><line x1="20" y1="20" x2="20" y2="8"/><rect x="36" y="34" width="8" height="8"/>
    </svg>
    <h3>Dry Cleaning Drop Off</h3>
    <p>Do you have clothing or linens that are made from delicate fabrics that aren't machine washable?...<span class="more">[+]</span></p>
  </div>
  <div class="service" style="left:435px;top:360px">
    <svg width="62" height="62" viewBox="0 0 62 62" fill="none" stroke="var(--blue-deep)" stroke-width="2">
      <rect x="6" y="2" width="50" height="58"/><line x1="6" y1="12" x2="56" y2="12"/>
      <circle cx="30" cy="36" r="15"/><circle cx="30" cy="36" r="9"/><line x1="12" y1="7" x2="22" y2="7"/>
    </svg>
    <h3>Self Service Laundry</h3>
    <p>With over 40 well maintained self-service washers and dryers laundry will be a thing of the past!...<span class="more">[+]</span></p>
  </div>

  <svg class="abs" style="left:690px;top:105px" width="360" height="400" viewBox="0 0 360 400" aria-hidden="true">
    <circle cx="151" cy="16" r="9" fill="none" stroke="var(--blue-deep)" stroke-width="5"/>
    <circle cx="106" cy="45" r="5" fill="none" stroke="var(--blue-deep)" stroke-width="3.5"/>
    <circle cx="206" cy="47" r="5" fill="none" stroke="var(--blue-deep)" stroke-width="3.5"/>
    <circle cx="187" cy="222" r="162" fill="none" stroke="var(--blue-deep)" stroke-width="6"/>
  </svg>
  <div class="abs" role="img" aria-label="Photo of a row of stainless steel front-load washers in the laundromat" style="left:718px;top:166px;width:322px;height:322px;border-radius:50%;background:linear-gradient(160deg,#e6e4dc 0%,#b9bbbb 45%,#6f7478 100%)"></div>
</section>

<!-- testimonials -->
<div class="testimonials-title">
  <h2 class="sec-title">Customer <span>Testimonials</span></h2>
  <div class="title-bar"></div>
</div>

<div class="card" style="left:162px">
  <div class="quote-badge">&rdquo;</div>
  <h4>Marla Quinby</h4>
  <p>Great drop off laundry location to have professionals do your laundry. They are quick, honor requests about how to bag it up, and are friendly and reasonable.</p>
  <div class="card-plus">+</div>
</div>
<div class="card" style="left:462px">
  <div class="quote-badge active">&rdquo;</div>
  <h4>Desmond Kr</h4>
  <p>Great customer service, friendly staff, the place looks clean &amp; they have the option to pay with your phone &amp; coins, great acco-mmodating to the customers. Thank you!</p>
  <div class="card-plus">+</div>
</div>
<div class="card" style="left:762px">
  <div class="quote-badge">&rdquo;</div>
  <h4>Tobias Renfield</h4>
  <p>This is one of the cleanest and friendly Coin Laundromats I've ever been too. Great place!</p>
  <div class="card-plus">+</div>
</div>
<div class="dots"><i></i><i></i><i class="on"></i><i></i></div>

<!-- footer -->
<footer class="site-footer">
  <div class="footer-brand">SUDS HAVEN</div>
  <div class="footer-line" style="left:310px;top:198px;width:580px"></div>
  <nav class="footer-nav">
    <a href="#" style="left:255px">Home</a>
    <a href="#" style="left:338px">About Us</a>
    <a href="#" style="left:446px">Services</a>
    <a href="#" style="left:549px">Locations</a>
    <a href="#" style="left:659px">Reviews</a>
    <a href="#" style="left:762px">Contact Us</a>
  </nav>
  <div class="soc" style="left:878px">Fb</div>
  <div class="soc" style="left:924px">Tw</div>

  <svg class="abs" style="left:246px;top:310px" width="18" height="18" viewBox="0 0 18 18" fill="none" stroke="#fff" stroke-width="1.3" aria-hidden="true">
    <circle cx="9" cy="9" r="7.5"/><path d="M1.5 9 H16.5 M9 1.5 C5 6 5 12 9 16.5 C13 12 13 6 9 1.5"/>
  </svg>
  <div class="contact-line" style="left:277px;top:306px">Brookvale Plaza, 2210 Linden Ave NE.,<br># 118, Atlanta, GA 30399</div>
  <svg class="abs" style="left:246px;top:370px" width="18" height="18" viewBox="0 0 18 18" fill="none" stroke="#fff" stroke-width="1.3" aria-hidden="true">
    <path d="M3 2 L6 2 L7.5 6 L5.5 7.5 C6.5 10 8 11.5 10.5 12.5 L12 10.5 L16 12 L16 15 C16 16 15 16.5 14 16.5 C7 16 2 11 1.5 4 C1.5 3 2 2 3 2 Z"/>
  </svg>
  <div class="contact-line" style="left:275px;top:366px">(404) 555-0192</div>

  <div class="hours">
    <span class="note">Delivery Available* please contact us for details</span><br>
    <span style="display:block;margin-top:8px">Covid 19 hours - open 7 days a week 8 am to 8 pm<br>Last wash begins 6:30 pm</span>
  </div>

  <div class="footer-line" style="left:162px;top:418px;width:876px"></div>
  <div class="copyright">Copyright &copy; 2021 <b>Suds Haven Atlanta</b>. All Rights Reserved.</div>
</footer>

</body>
</html>
```